ultra-minimalist business card

front (black background, matte):

reza t. kovin
writer | photographer
get@rezakovin.com

back (white background, matte):

a picture speaks a thousand words;
a word draws a thousand pictures.

www.rezakovin.com

all text should be small (white or silver - as long as it shows against the black - on the front; black or gray - as long as it shows against the white - on the back).

feel free to get creative in terms of arrangement, alignment, and font type, but remember, the overall style is minimalist, so nothing too fancy, please.

thanks.

```html
<!DOCTYPE html>
<html lang="en">
<head>
<meta charset="utf-8">
<title>Reza T. Kovin — Business Card</title>
<link rel="stylesheet" href="https://fonts.googleapis.com/css2?family=Libre+Baskerville:wght@400;700&family=Montserrat:wght@400;500&display=swap">
<style>
  :root {
    --stage: #2a2b2d;
    --card-front: #16181a;
    --card-back: #ffffff;
    --silver-light: #eceded;
    --silver-mid: #aeb1b4;
    --silver-dark: #74777b;
    --text-white: #f2f2f2;
    --text-grey: #b9bcbf;
    --ink: #1a1b1d;
    --ink-grey: #6b6e72;
  }
  * { margin: 0; padding: 0; box-sizing: border-box; }
  html, body {
    width: 1200px;
    height: 1000px;
    overflow: hidden;
    background: var(--stage);
  }
  .stage {
    width: 1200px;
    height: 1000px;
    display: flex;
    flex-direction: column;
    align-items: center;
    justify-content: center;
    gap: 70px;
  }
  .card {
    position: relative;
    width: 600px;
    height: 343px;
    box-shadow: 0 10px 30px rgba(0,0,0,0.45);
  }
  .card--back { background: var(--card-back); }
  .card--front { background: var(--card-front); }

  .silver {
    background: linear-gradient(180deg, var(--silver-light) 0%, var(--silver-mid) 45%, var(--silver-dark) 60%, var(--silver-light) 100%);
    -webkit-background-clip: text;
    background-clip: text;
    color: transparent;
  }

  /* back: quote + website */
  .quote {
    position: absolute;
    right: 44px;
    bottom: 72px;
    text-align: right;
    font-family: "Montserrat", sans-serif;
    font-size: 13px;
    line-height: 1.4;
    color: var(--ink);
    letter-spacing: 0.02em;
  }
  .website {
    position: absolute;
    right: 44px;
    bottom: 40px;
    font-family: "Montserrat", sans-serif;
    font-size: 13px;
    color: var(--ink-grey);
    letter-spacing: 0.03em;
  }

  /* front: identity + email */
  .identity {
    position: absolute;
    left: 52px;
    bottom: 62px;
  }
  .identity__name {
    font-family: "Libre Baskerville", serif;
    font-weight: 700;
    font-size: 22px;
    letter-spacing: 0.01em;
  }
  .identity__role {
    margin-top: 4px;
    font-family: "Montserrat", sans-serif;
    font-size: 15px;
    color: var(--text-grey);
    letter-spacing: 0.03em;
  }
  .contact {
    position: absolute;
    left: 330px;
    top: 72px;
    font-family: "Montserrat", sans-serif;
    font-size: 14px;
    color: var(--text-white);
    list-style: none;
  }
  .contact__label {
    display: inline-block;
    width: 28px;
    font-weight: 500;
    color: var(--silver-light);
  }
</style>
</head>
<body>
  <main class="stage">
    <section class="card card--back">
      <p class="quote">a picture speaks a thousand words;<br>a word draws a thousand pictures.</p>
      <p class="website">www.rezakovin.com</p>
    </section>

    <section class="card card--front">
      <ul class="contact">
        <li><span class="contact__label">E:</span>get@rezakovin.com</li>
      </ul>
      <div class="identity">
        <p class="identity__name silver">reza t. kovin</p>
        <p class="identity__role">writer | photographer</p>
      </div>
    </section>
  </main>
</body>
</html>
```